Stylish new business card needed!

Hello everyone! I am in need of a new business card design for an alarm company here in Hurricane WV. I have all fonts, color codes and logos provided for you use! We are a young company and like the style of a clean sleek looking business card. Would like it double sided, one side holding the logo and the other with your design!
Target Market(s)
The people that are looking for the newest tech for home automation and security
Industry/Entity Type
Alarm services; Home automation
Contact Information for Business Card
Name of person; position (Sales; Installer); Phone Number (555.418.7260); Employee cell Number; Website (www.GuardedByVelk.example); Employee Email; Double sided
Look and feel
Each slider illustrates characteristics of the customer's brand and the style your logo design should communicate.

```html
<!DOCTYPE html>
<html lang="en">
<head>
<meta charset="utf-8">
<title>Velk Business Card</title>
<link href="https://fonts.googleapis.com/css2?family=Arimo:wght@400;700&display=swap" rel="stylesheet">
<style>
  :root {
    --bg: #161616;
    --card-dark: #2a2a2a;
    --orange: #f47a36;
    --orange-light: #f98f48;
    --paper: #f7f6f3;
    --grey: #8a8a8a;
    --text-grey: #6e6e6e;
  }
  * { box-sizing: border-box; margin: 0; padding: 0; }
  html, body {
    width: 1200px; height: 963px; overflow: hidden;
    background: var(--bg);
    font-family: "Arimo", Arial, sans-serif;
  }
  .sheet {
    display: flex; gap: 80px;
    justify-content: center; align-items: center;
    width: 1200px; height: 963px;
  }
  .card {
    position: relative;
    width: 460px; height: 805px;
    border-radius: 34px;
    overflow: hidden;
    box-shadow: 0 0 0 3px var(--orange), 0 20px 50px rgba(0,0,0,.6);
  }
  /* Front */
  .card--front { background: var(--paper); }
  .front__band {
    height: 330px;
    background: linear-gradient(135deg, var(--orange) 0%, var(--orange-light) 100%);
    display: flex; align-items: center; justify-content: center; gap: 18px;
  }
  .brand-dot {
    width: 42px; height: 42px; border-radius: 50%;
    background: var(--paper);
  }
  .brand-name--front {
    font-weight: 700; font-size: 96px; letter-spacing: 4px;
    color: var(--paper); line-height: 1;
  }
  .front__body { padding: 34px 48px 0; }
  .tagline {
    font-weight: 700; font-size: 15px; letter-spacing: 1.4px;
    color: var(--orange); text-transform: uppercase; text-align: center;
  }
  .person { margin-top: 120px; }
  .person__name {
    font-weight: 700; font-size: 38px; color: var(--orange);
    text-transform: uppercase; letter-spacing: 1px; line-height: 1;
  }
  .person__role { font-size: 27px; color: var(--text-grey); margin-top: 6px; }
  .icons { display: flex; gap: 14px; margin-top: 30px; }
  .icons svg { width: 38px; height: 38px; }
  .contact { margin-top: 30px; list-style: none; }
  .contact li {
    font-size: 24px; color: var(--text-grey); line-height: 1.55;
  }
  /* Back */
  .card--back {
    background: var(--card-dark);
    display: flex; align-items: center; justify-content: center; gap: 20px;
  }
  .brand-name--back {
    font-weight: 700; font-size: 110px; letter-spacing: 6px;
    color: var(--grey); line-height: 1;
  }
  .card--back .brand-dot { background: var(--orange); width: 48px; height: 48px; }
</style>
</head>
<body>
<main class="sheet">
  <section class="card card--front" aria-label="Card front">
    <header class="front__band">
      <span class="brand-dot"></span>
      <span class="brand-name--front">Velk</span>
    </header>
    <div class="front__body">
      <p class="tagline">Automation and Security Services</p>
      <div class="person">
        <h1 class="person__name">Marcus Hale</h1>
        <p class="person__role">Sales / Installer</p>
      </div>
      <div class="icons" aria-hidden="true">
        <svg viewBox="0 0 38 38" fill="none" stroke="#f47a36" stroke-width="2">
          <circle cx="19" cy="19" r="17"/>
          <path d="M13 12l4 0 1 5-2 1.5a10 10 0 0 0 5 5l1.5-2 5 1 0 4c-8 1-15-6-14.5-14.5z" stroke-linejoin="round"/>
        </svg>
        <svg viewBox="0 0 38 38" fill="none" stroke="#f47a36" stroke-width="2">
          <circle cx="19" cy="19" r="17"/>
          <rect x="10" y="13" width="18" height="12" rx="1"/>
          <path d="M10 13l9 7 9-7"/>
        </svg>
        <svg viewBox="0 0 38 38" fill="none" stroke="#f47a36" stroke-width="2">
          <circle cx="19" cy="19" r="17"/>
          <circle cx="19" cy="19" r="9"/>
          <ellipse cx="19" cy="19" rx="4" ry="9"/>
          <path d="M10 19h18M12 14h14M12 24h14"/>
        </svg>
      </div>
      <ul class="contact">
        <li>555.418.7260</li>
        <li>info@GuardedByVelk.example</li>
        <li>www.GuardedByVelk.example</li>
      </ul>
    </div>
  </section>

  <section class="card card--back" aria-label="Card back">
    <span class="brand-dot"></span>
    <span class="brand-name--back">Velk</span>
  </section>
</main>
</body>
</html>
```